Im open to ideas.. I was thinking on my business cards aswell as my logo. a place for my name. email. phone number and abn..

ive attched a file with my business logo. which i dont love the colours.. i was think a dark background with charcoal letters so something along those colour schumes but im open to ideas..

BRM Constructions

```html
<!DOCTYPE html>
<html lang="en">
<head>
<meta charset="UTF-8">
<title>BRM Constructions – Business Card</title>
<link href="https://fonts.googleapis.com/css2?family=Open+Sans:wght@400;600;700;800&display=swap" rel="stylesheet">
<style>
  :root {
    --backdrop: #e7e4e1;
    --card-face: #f7f7f7;
    --charcoal: #4f4f4f;
    --ink: #1f1f1f;
    --muted: #3a3a3a;
    --divider: #8a8a8a;
    --band: #565656;
    --band-text: #ffffff;
  }
  * { margin: 0; padding: 0; box-sizing: border-box; }
  html, body {
    width: 1200px;
    height: 900px;
    overflow: hidden;
    background: var(--backdrop);
    font-family: "Open Sans", Arial, sans-serif;
  }
  .canvas {
    position: relative;
    width: 1200px;
    height: 900px;
  }
  .business-card {
    position: absolute;
    left: 275px;
    top: 250px;
    width: 650px;
    height: 400px;
    border-radius: 18px;
    overflow: hidden;
    background: var(--card-face);
    box-shadow: 0 6px 24px rgba(0,0,0,0.12);
  }
  .brand-name {
    position: absolute;
    top: 100px;
    left: 0;
    width: 100%;
    text-align: center;
    font-size: 58px;
    font-weight: 800;
    color: var(--charcoal);
    letter-spacing: 1px;
    line-height: 1;
  }
  .holder {
    position: absolute;
    top: 243px;
    right: 342px;
    text-align: right;
  }
  .holder-name {
    font-size: 25px;
    font-weight: 600;
    color: var(--ink);
    line-height: 1.2;
  }
  .holder-title {
    font-size: 17px;
    font-weight: 400;
    color: var(--muted);
    margin-top: 1px;
  }
  .divider {
    position: absolute;
    left: 325px;
    top: 240px;
    width: 1px;
    height: 64px;
    background: var(--divider);
  }
  .contact-list {
    position: absolute;
    left: 342px;
    top: 234px;
    list-style: none;
  }
  .contact-item {
    display: flex;
    align-items: center;
    gap: 7px;
    font-size: 17px;
    color: var(--ink);
    line-height: 23px;
  }
  .contact-icon {
    width: 12px;
    height: 12px;
    fill: var(--ink);
  }
  .abn-band {
    position: absolute;
    left: 0;
    bottom: 0;
    width: 100%;
    height: 74px;
    background: var(--band);
    color: var(--band-text);
    display: flex;
    align-items: center;
    justify-content: center;
    font-size: 16px;
  }
  .abn-label { font-weight: 700; }
</style>
</head>
<body>
<main class="canvas">
  <section class="business-card">
    <div class="brand-name">BRM Constructions</div>

    <div class="holder">
      <div class="holder-name">Daniel Harper</div>
      <div class="holder-title">Managing Director</div>
    </div>

    <div class="divider"></div>

    <ul class="contact-list">
      <li class="contact-item">
        <svg class="contact-icon" viewBox="0 0 12 12" aria-hidden="true">
          <path d="M1 4 Q6 0 11 4 L9.5 5.5 L8 4.2 L4 4.2 L2.5 5.5 Z"/>
          <rect x="2.5" y="5.5" width="7" height="5" rx="1"/>
        </svg>
        <span>044-987 654 321</span>
      </li>
      <li class="contact-item">
        <svg class="contact-icon" viewBox="0 0 12 12" aria-hidden="true">
          <rect x="0.5" y="2.5" width="11" height="7.5" rx="0.8"/>
          <path d="M1 3 L6 7 L11 3" fill="none" stroke="#f7f7f7" stroke-width="1"/>
        </svg>
        <span>info@brmbuild.com</span>
      </li>
      <li class="contact-item">
        <svg class="contact-icon" viewBox="0 0 12 12" aria-hidden="true">
          <circle cx="6" cy="6" r="5.5"/>
          <path d="M3 4 Q5 3 6 5 Q5 7 7 8 M8 3 Q9 5 8.5 6" fill="none" stroke="#f7f7f7" stroke-width="1"/>
        </svg>
        <span>www.brmbuild.com</span>
      </li>
    </ul>

    <footer class="abn-band">
      <span class="abn-label">ABN:</span><span class="abn-number">7654321</span>
    </footer>
  </section>
</main>
</body>
</html>
```